Mailing Brochure

I need a cover for a brochure that we are doing here locally. The only thing I am worried about is the COVER. The size of the brochure is 8.5 x 11 in.
We have a reasonable design for the inserts and back cover. We will mail the packet to accident victims that may need a lawyer. I am including a copy of our current tri-fold brochure that this will replace. The copy from that brochure will be in the inserts. We want something a little similar to that brochure- emphasizing good results and happy people, with maybe a little more legal flavor. I have included photos Pilgrave and the firm's building.
Thanks for your help.

```html
<!DOCTYPE html>
<html lang="en">
<head>
<meta charset="UTF-8">
<title>Pilgrave Law Group – Brochure Cover</title>
<link rel="stylesheet" href="https://fonts.googleapis.com/css2?family=Montserrat:wght@300;400;600;700;800&display=swap">
<style>
  :root {
    --navy: #0f3f73;
    --navy-deep: #0b2f5a;
    --brand-blue: #1b5486;
    --slate: #58585a;
    --paper: #ffffff;
    --backdrop: #2f2f31;
    --hairline: rgba(255, 255, 255, 0.55);
  }
  * { margin: 0; padding: 0; box-sizing: border-box; }
  html, body {
    width: 1200px; height: 900px; overflow: hidden;
    background: var(--backdrop);
    font-family: "Montserrat", sans-serif;
  }
  .cover {
    position: absolute; left: 268px; top: 20px;
    width: 664px; height: 860px;
    background: var(--paper);
    overflow: hidden;
    box-shadow: 0 18px 40px rgba(0, 0, 0, 0.45);
  }

  .brand {
    position: absolute; top: 64px; left: 0; width: 100%;
    display: flex; justify-content: center; align-items: center; gap: 12px;
  }
  .brand-square { width: 70px; height: 62px; background: var(--brand-blue); }
  .brand-name {
    color: var(--brand-blue); font-weight: 400;
    font-size: 25px; line-height: 1.1; letter-spacing: 2px; text-transform: uppercase;
  }

  .tile { position: absolute; overflow: hidden; }

  .headline-box {
    left: 0; top: 170px; width: 300px; height: 200px;
    background: var(--brand-blue); color: #fff;
    padding: 46px 20px 0 40px;
    font-size: 27px; font-weight: 300; line-height: 1.22;
  }
  .headline-box strong { font-weight: 800; }

  .photo { background-color: #9aa7b4; }
  .photo::after {
    content: ""; position: absolute; inset: 0;
    background-image:
      linear-gradient(var(--hairline), var(--hairline)),
      linear-gradient(var(--hairline), var(--hairline));
    background-size: 1px 100%, 100% 1px;
    background-repeat: no-repeat;
  }
  .photo-ski {
    left: 300px; top: 150px; width: 364px; height: 400px;
    background:
      radial-gradient(ellipse 60% 55% at 62% 58%, #2f56a0 0%, rgba(47, 86, 160, 0.6) 45%, rgba(47, 86, 160, 0) 75%),
      radial-gradient(ellipse 30% 60% at 6% 35%, #4a5a4e 0%, rgba(74, 90, 78, 0) 100%),
      linear-gradient(170deg, #b9c6d3 0%, #e4eaf0 45%, #f4f6f8 100%);
  }
  .photo-ski::after { background-position: 38% 0, 0 38%; }

  .photo-fishing {
    left: 0; top: 370px; width: 380px; height: 320px;
    background:
      radial-gradient(ellipse 45% 55% at 42% 62%, #5f8cc4 0%, rgba(95, 140, 196, 0.55) 45%, rgba(95, 140, 196, 0) 80%),
      radial-gradient(ellipse 70% 35% at 50% 20%, #8fa0a4 0%, rgba(143, 160, 164, 0) 100%),
      linear-gradient(180deg, #8aa07e 0%, #7fae55 55%, #4d6e3a 100%);
  }
  .photo-fishing::after { background-position: 22% 0, 0 55%; }

  .tagline-box {
    left: 380px; top: 550px; width: 150px; height: 140px;
    background: var(--slate); color: #f1f1f1;
    display: flex; align-items: center; justify-content: center; text-align: center;
    font-size: 14px; font-weight: 300; line-height: 1.6; padding: 0 10px;
  }

  .photo-hiking {
    left: 530px; top: 530px; width: 134px; height: 160px;
    background:
      radial-gradient(ellipse 45% 50% at 45% 65%, #c4d83a 0%, rgba(196, 216, 58, 0) 100%),
      radial-gradient(ellipse 40% 60% at 80% 50%, #2b2b2b 0%, rgba(43, 43, 43, 0) 100%),
      linear-gradient(160deg, #6d7d5e 0%, #8f9a86 60%, #5f6c55 100%);
  }
  .photo-hiking::after { background-position: 60% 0, 0 78%; }

  .footer-band { position: absolute; left: 0; top: 665px; width: 664px; height: 195px; }

  .contact {
    position: absolute; left: 0; top: 738px; width: 100%;
    text-align: center; color: var(--navy-deep);
  }
  .contact-phone { font-size: 36px; font-weight: 800; letter-spacing: 1px; line-height: 1.1; }
  .contact-address { font-size: 16px; font-weight: 600; margin-top: 8px; }
  .contact-web { font-size: 16px; font-weight: 600; margin-top: 6px; }
</style>
</head>
<body>
  <main class="cover">
    <header class="brand">
      <span class="brand-square"></span>
      <span class="brand-name">Pilgrave<br>Law Group</span>
    </header>

    <div class="tile photo photo-ski" role="img" aria-label="Photo of a smiling family on cross-country skis in falling snow"></div>
    <div class="tile headline-box">We’ll help you<br>get <strong>back to<br>what you love</strong></div>
    <div class="tile photo photo-fishing" role="img" aria-label="Photo of a father and young son fishing by a lake"></div>
    <div class="tile tagline-box">Helping Accident<br>Victims since 1993</div>
    <div class="tile photo photo-hiking" role="img" aria-label="Photo of a couple hiking with binoculars and a map"></div>

    <svg class="footer-band" viewBox="0 0 664 195" preserveAspectRatio="none" aria-hidden="true">
      <defs>
        <linearGradient id="footerFade" x1="0" y1="0" x2="0" y2="1">
          <stop offset="0" stop-color="#ffffff"/>
          <stop offset="1" stop-color="#e8ebee"/>
        </linearGradient>
      </defs>
      <path d="M0 30 Q 330 22 664 0 L664 195 L0 195 Z" fill="url(#footerFade)"/>
      <path d="M0 30 Q 330 22 664 0" fill="none" stroke="#0f3f73" stroke-width="4"/>
    </svg>

    <section class="contact">
      <div class="contact-phone">907 555 0148</div>
      <div class="contact-address">412 K Street • Anchorage, AK 99501</div>
      <div class="contact-web">www.pilgravelaw.com</div>
    </section>
  </main>
</body>
</html>
```